Veranix - Solution provider in business consulting

Veranix is a swiss based company providing solutions for developing markets. The business covers various fields of business consulting, such as supply chain, product costs, quality management and manufacturing management. The Business operates in a efficient, straight and solution oriented manner.
The final design should communicate these characteristics. Asian people as well as as western people shall identify the qualities of the company at first sight.
The customer needs business cards with a simple view but an recognizable design, printed in high quality. Engraved elements such as the globe or simple words are possible.
Available colors are: (RAL)
102/102/102
51/102/102
153/204/153
255/102/51
Font: Calibri

```html
<!DOCTYPE html>
<html lang="en">
<head>
<meta charset="utf-8">
<title>Veranix business cards</title>
<link href="https://fonts.googleapis.com/css2?family=Carlito:wght@400;700&display=swap" rel="stylesheet">
<style>
  :root {
    --bg-top: #2b2b2b;
    --bg-bottom: #060606;
    --card-front: #ffffff;
    --card-back: #666666;
    --ink: #666666;
    --ink-strong: #4a4a4a;
    --mark-light: #ffffff;
  }
  html, body {
    margin: 0;
    padding: 0;
    width: 1200px;
    height: 900px;
    overflow: hidden;
  }
  body {
    position: relative;
    background: linear-gradient(180deg, var(--bg-top) 0%, #151515 55%, var(--bg-bottom) 100%);
    font-family: "Carlito", "Calibri", sans-serif;
  }
  .card {
    position: absolute;
    top: 306px;
    width: 439px;
    height: 271px;
    border-radius: 12px;
  }
  .card--front { left: 149px; background: var(--card-front); }
  .card--back { left: 609px; width: 440px; background: var(--card-back); }

  .brand {
    position: absolute;
    display: flex;
    align-items: center;
    gap: 10px;
    font-weight: 400;
    letter-spacing: 0.5px;
  }
  .brand__dot { border-radius: 50%; flex: none; }
  .card--front .brand {
    left: 34px;
    top: 112px;
    color: var(--ink);
    font-size: 38px;
  }
  .card--front .brand__dot { width: 22px; height: 22px; background: var(--ink); }
  .card--back .brand {
    left: 0;
    right: 0;
    top: 100px;
    justify-content: center;
    color: var(--mark-light);
    font-size: 56px;
  }
  .card--back .brand__dot { width: 32px; height: 32px; background: var(--mark-light); }

  .contact {
    position: absolute;
    left: 247px;
    top: 50px;
    color: var(--ink);
    font-size: 13px;
    line-height: 17px;
  }
  .contact__name {
    margin: 0;
    font-size: 17px;
    font-weight: 700;
    color: var(--ink-strong);
    line-height: 20px;
  }
  .contact__role { margin: 0 0 12px; }
  .contact__address { margin: 0 0 15px; font-style: normal; }
  .contact__list { list-style: none; margin: 0; padding: 0; }
  .contact__item {
    display: flex;
    align-items: center;
    height: 18px;
  }
  .contact__icon {
    width: 9px;
    height: 9px;
    margin-right: 8px;
    fill: var(--ink);
    flex: none;
  }
</style>
</head>
<body>
  <section class="card card--front">
    <div class="brand"><span>veranix</span><span class="brand__dot"></span></div>
    <div class="contact">
      <p class="contact__name">Marco Lenz</p>
      <p class="contact__role">CEO</p>
      <address class="contact__address">Veranix GmbH Talstrasse 18<br>9100 Herisau Switzerland</address>
      <ul class="contact__list">
        <li class="contact__item">
          <svg class="contact__icon" viewBox="0 0 10 10" aria-hidden="true"><path d="M2.5 0h5a1 1 0 0 1 1 1v8a1 1 0 0 1-1 1h-5a1 1 0 0 1-1-1V1a1 1 0 0 1 1-1zm.5 1.5v6h4v-6zM5 8.3a.6.6 0 1 0 0 1.2.6.6 0 0 0 0-1.2z"/></svg>
          +41 79 555 0142
        </li>
        <li class="contact__item">
          <svg class="contact__icon" viewBox="0 0 10 10" aria-hidden="true"><path d="M2 0.3l1.6 2.1-.9 1.1a6 6 0 0 0 3.8 3.8l1.1-.9L9.7 8 8.6 9.6C4.5 9.8.2 5.5.4 1.4z"/></svg>
          +41 71 555 0187
        </li>
        <li class="contact__item">
          <svg class="contact__icon" viewBox="0 0 10 10" aria-hidden="true"><path d="M0 2h10v.6L5 5.6 0 2.6zM0 3.6l5 3 5-3V8H0z"/></svg>
          marco.lenz@veranix.ch
        </li>
        <li class="contact__item">
          <svg class="contact__icon" viewBox="0 0 10 10" aria-hidden="true"><path d="M5 0a5 5 0 1 0 0 10A5 5 0 0 0 5 0zm0 1a4 4 0 0 1 3.9 3.5H7A6 6 0 0 0 5.6 1.1 4 4 0 0 1 5 1zM4.4 1.1A6 6 0 0 0 3 4.5H1.1A4 4 0 0 1 4.4 1.1zM4 4.5A5 5 0 0 1 5 1.6a5 5 0 0 1 1 2.9zm-2.9 1H3a6 6 0 0 0 1.4 3.4A4 4 0 0 1 1.1 5.5zm2.9 0h2A5 5 0 0 1 5 8.4a5 5 0 0 1-1-2.9zm3 0h1.9a4 4 0 0 1-3.3 3.4A6 6 0 0 0 7 5.5z"/></svg>
          www.veranix.ch
        </li>
      </ul>
    </div>
  </section>

  <section class="card card--back">
    <div class="brand"><span>veranix</span><span class="brand__dot"></span></div>
  </section>
</body>
</html>
```